New name flyer

We have just changed our business name from kR Property group to Harbor Lantern. We want to distribute a flyer to the local community to inform them of the change. We are a realestate agency which focuses mainly on property management but also sales. We service from Brisbane to the Sunshine coast.

Target Market(s)

Local community

Industry/Entity Type

realestate

Requirements
Must have
• Details of name change
Nice to have
• Servicing area Brisbane and Sunshine Coast, no change in management or services we offer, and will continue pride ourselves on offering a high level of service, with the same team from the Gold to Sunshine Coast.
Should not have
• too much wording.

```html
<!DOCTYPE html>
<html lang="en">
<head>
<meta charset="utf-8">
<title>Harbor Lantern – New Name Flyer</title>
<link rel="stylesheet" href="https://fonts.googleapis.com/css2?family=Roboto+Condensed:wght@400;700&family=Montserrat:wght@800&display=swap">
<style>
  :root {
    --paint-gold: #cca457;
    --text-gold: #c49a1c;
    --navy: #0f1a63;
    --deep-navy: #0f2340;
    --paper: #ffffff;
    --frame: #9a9a9a;
  }
  html, body {
    margin: 0;
    padding: 0;
    overflow: hidden;
    background: var(--paper);
  }
  .flyer {
    position: relative;
    width: 1200px;
    height: 825px;
    overflow: hidden;
    background: var(--paper);
    box-sizing: border-box;
    border: 1px solid var(--frame);
    font-family: "Roboto Condensed", "Arial Narrow", sans-serif;
  }
  .painted-wall-art {
    position: absolute;
    left: 0;
    top: 0;
    width: 100%;
    height: 300px;
    background: linear-gradient(180deg, var(--paint-gold) 0%, #d2ad66 100%);
  }
  .former-brand {
    position: absolute;
    left: 400px;
    top: 120px;
    display: flex;
    align-items: center;
    gap: 12px;
  }
  .former-brand__square {
    width: 56px;
    height: 56px;
    background: var(--navy);
  }
  .former-brand__name {
    font-weight: 400;
    font-size: 34px;
    color: var(--navy);
    line-height: 1;
  }
  .painter-art {
    position: absolute;
    left: 38px;
    top: 330px;
    width: 160px;
    height: 490px;
    background: linear-gradient(180deg, #f5c928 0%, #1a2a4a 22%, #0f2340 100%);
    border-radius: 40px 40px 6px 6px;
  }
  .paint-cans-art {
    position: absolute;
    left: 189px;
    top: 758px;
    width: 107px;
    height: 62px;
    background: linear-gradient(90deg, #0f1a63 0%, #3a6db5 45%, #c4961a 55%, #e0c47a 100%);
    border-radius: 3px;
  }
  .new-brand {
    position: absolute;
    left: 262px;
    top: 488px;
    margin: 0;
    font-family: "Montserrat", "Arial Black", sans-serif;
    font-weight: 800;
    font-size: 60px;
    line-height: 1.08;
    letter-spacing: 2px;
    color: var(--navy);
    text-transform: uppercase;
  }
  .announcement {
    position: absolute;
    left: 764px;
    top: 448px;
    width: 420px;
  }
  .announcement__old {
    margin: 0;
    font-size: 44px;
    font-weight: 400;
    line-height: 1.08;
    color: var(--text-gold);
  }
  .announcement__new {
    margin: 6px 0 0;
    font-size: 52px;
    font-weight: 700;
    line-height: 1;
    color: var(--navy);
    text-transform: uppercase;
  }
  .announcement__details {
    margin: 66px 0 0 3px;
    font-size: 19px;
    font-weight: 700;
    line-height: 1.25;
    color: var(--navy);
  }
  .announcement__area {
    margin: 25px 0 0 3px;
    font-size: 19px;
    font-weight: 700;
    color: var(--navy);
  }
</style>
</head>
<body>
  <main class="flyer">
    <div class="painted-wall-art" role="img" aria-label="Illustration of the wall being painted over in gold with a roller"></div>

    <div class="former-brand">
      <span class="former-brand__square"></span>
      <span class="former-brand__name">kR Property group</span>
    </div>

    <div class="painter-art" role="img" aria-label="Illustration of a worker in a hard hat and suit rolling paint onto the wall"></div>
    <div class="paint-cans-art" role="img" aria-label="Illustration of two open paint tins, navy and gold"></div>

    <h1 class="new-brand">Harbor<br>Lantern</h1>

    <section class="announcement">
      <p class="announcement__old">kR Property Group<br>is now</p>
      <h2 class="announcement__new">Harbor Lantern</h2>
      <p class="announcement__details">We've changed our name.<br>No change in management or services we offer.</p>
      <p class="announcement__area">We service from Brisbane to the Sunshine coast.</p>
    </section>
  </main>
</body>
</html>
```